Design Website Templates for Photographers for Lumera Inc. (trylumera.example)

Lumera Inc. is a generative website company for wedding photographers.
We are seeking new photography website design inspirations for the next template to be offered on our platform. The catch is you must use the same data for your designs. You also must use all of the data somewhere in the design. You cannot add new content besides the data available. If you wish to add any elements It will be hardcoded and must be universally fitting for many different photographers. We recommend not using any hardcoded test.
Don't be afraid to be creative! Although the most important element of a photographers website is the photos, we are looking for unique and out-of-the-box designs for the actual site as well.
Here is the User generated data available to you:
- 4 Hero Images Landscape, 4 Hero Images Portrait
- Tagline “destination photographer based in Maui, Hawaii”
- “About Photo” of the photographer
- “About” Biography Text
- The design can use up to 3 colors + background color and 2 fonts
- 9 Gallery images
- 3 Packages/services that include landscape/portrait images, a price, a title and text
- Testimonials made up of an image, text and text for the name of testimonial giver
See some examples of our current website designs attached. You can use any of the data you see in the designs.
Updates
We are looking for designs that are less feminine and are more neutral in color and fonts. Currently our templates are more oriented towards feminine photographers. We want to have designs that speak to diverse audiences. We thank everyone for submitting and are reviewing the designs.
Number of Pages Required
1 page
Look and feel
Each slider illustrates characteristics of the customer's brand and the style your logo design should communicate.

```html
<!DOCTYPE html>
<html lang="en">
<head>
<meta charset="utf-8">
<title>Lumera — Destination Photographer</title>
<link href="https://fonts.googleapis.com/css2?family=Alegreya+Sans:ital,wght@1,800&family=Poppins:wght@400;500;600&display=swap" rel="stylesheet">
<style>
:root{
  --accent:#f2b233;
  --ink:#222222;
  --text:#333333;
  --white:#ffffff;
  --dark:#29272b;
  --muted:#d9d9d9;
}
*{margin:0;padding:0;box-sizing:border-box}
html,body{width:1200px;height:4815px;overflow:hidden;background:var(--white)}
body{position:relative;font-family:"Poppins",sans-serif;color:var(--text)}
.abs{position:absolute}
.photo{position:absolute;border-radius:10px;overflow:hidden}
.display{font-family:"Alegreya Sans",sans-serif;font-style:italic;font-weight:800}
.section-title{position:absolute;left:0;width:1200px;text-align:center;color:var(--accent);font-size:42px;line-height:1}
.btn-outline{position:absolute;display:flex;align-items:center;justify-content:center;border:2px solid var(--accent);color:var(--accent);font-size:14px;border-radius:3px}

/* hero */
.hero{left:0;top:0;width:1200px;height:686px;background:linear-gradient(180deg,#3c4a30 0%,#4f5e34 40%,#6f7a3d 75%,#4d5a2c 100%)}
.hero-shade{left:0;top:0;width:1200px;height:686px;background:rgba(0,0,0,.35)}
.brand{left:108px;top:30px;font-size:56px;font-weight:600;color:var(--white);letter-spacing:2px;line-height:1}
.nav{top:48px;display:flex;gap:0;font-size:14px;color:var(--white)}
.nav a{position:absolute;color:inherit;text-decoration:none;white-space:nowrap}
.book{left:957px;top:36px;width:129px;height:37px;border:2px solid var(--white);color:var(--white);font-size:14px;display:flex;align-items:center;justify-content:center;border-radius:2px}
.tagline{left:0;top:205px;width:1200px;text-align:center;color:var(--white);font-size:78px;line-height:85px}
.hero-btn{left:531px;top:510px;width:146px;height:38px;border:2px solid var(--white);color:var(--white);font-size:14px;display:flex;align-items:center;justify-content:center;border-radius:2px}
.arrow{top:333px}

/* about */
.about-card{left:572px;top:933px;width:516px;height:239px;background:var(--white);border-radius:8px;box-shadow:0 6px 24px rgba(0,0,0,.12);padding:30px 40px 0;text-align:center;font-size:14.5px;line-height:26px}
.frame{border:5px solid var(--accent);border-radius:10px}
.dots{display:flex;gap:5px}
.dots span{width:9px;height:9px;border-radius:50%;background:var(--accent)}

/* bio */
.bio-title{left:110px;top:1378px;color:var(--accent);font-size:42px}
.bio-text{left:110px;width:450px;font-size:14.5px;line-height:26px;color:var(--text)}

/* gallery */
.gallery-intro{left:240px;top:1990px;width:720px;text-align:center;font-size:14.5px;line-height:26px}

/* price */
.tab{position:absolute;top:3325px;height:74px;display:flex;align-items:center;justify-content:center;font-size:26px}
.price-band{left:0;top:3364px;width:1200px;height:410px;background:linear-gradient(90deg,#1f1d1a,#3a3a30 50%,#1f1f1d)}
.price-card{position:absolute;top:3461px;width:286px;height:249px;background:var(--white);border-radius:6px;text-align:center;padding-top:28px}
.price-card h3{color:var(--accent);font-size:27px;line-height:1}
.price-card p{font-size:14.5px;line-height:26px;margin:18px 26px 0}
.price-card strong{display:block;margin-top:14px;font-size:25px;font-weight:600;color:var(--ink)}

/* testimonials */
.quote-text{left:670px;top:4008px;width:400px;text-align:center;font-size:14.5px;line-height:26px}
.quote-mark{color:var(--accent);font-size:42px;line-height:1}
.avatar{position:absolute;border-radius:50%;border:3px solid var(--white)}

/* footer */
.footer{left:0;top:4471px;width:1200px;height:344px;background:var(--dark);color:var(--white)}
.footer-brand{left:0;top:4508px;width:1200px;text-align:center;font-size:96px;font-weight:600;letter-spacing:4px;line-height:1;color:var(--white)}
.footer-nav a{position:absolute;top:4643px;color:var(--white);font-size:14px;text-decoration:none}
.social{position:absolute;top:4691px;width:16px;height:16px;border-radius:50%;background:var(--white)}
.footer-rule{left:0;top:4747px;width:1200px;height:1px;background:#5a585c}
.copyright{left:0;top:4772px;width:1200px;text-align:center;font-size:13px;color:var(--white)}
</style>
</head>
<body>

<!-- Hero -->
<section>
  <div class="abs hero" role="img" aria-label="Photographer kneeling on a lawn shooting a bride at sunset"></div>
  <div class="abs hero-shade"></div>
  <div class="abs brand">LUMERA</div>
  <nav class="abs nav" style="left:0;top:48px">
    <a style="left:402px">Home</a>
    <a style="left:497px">Blog</a>
    <a style="left:579px">Testimonials</a>
    <a style="left:721px">Portfolio</a>
    <a style="left:830px">Get In Touch</a>
  </nav>
  <div class="abs book">Book With Me</div>
  <svg class="abs arrow" style="left:52px" width="26" height="40" viewBox="0 0 26 40"><path d="M20 4 L6 20 L20 36" fill="none" stroke="#fff" stroke-width="4"/></svg>
  <svg class="abs arrow" style="left:1125px" width="26" height="40" viewBox="0 0 26 40"><path d="M6 4 L20 20 L6 36" fill="none" stroke="#fff" stroke-width="4"/></svg>
  <h1 class="abs tagline display">“Destination<br>Photographer Based<br>in Maui, Hawaii”</h1>
  <div class="abs hero-btn">Get Started Here</div>
</section>

<!-- About Photo -->
<section>
  <h2 class="section-title display" style="top:766px">About Photo</h2>
  <div class="photo" style="left:110px;top:862px;width:600px;height:381px;background:linear-gradient(180deg,#c97a45 0%,#e7a05a 35%,#8a5a34 65%,#4b3722 100%)" role="img" aria-label="Wedding couple embracing on a hillside at sunset"></div>
  <div class="abs frame" style="left:553px;top:914px;width:467px;height:217px"></div>
  <div class="abs about-card">
    Lorem ipsum dolor sit amet, consectetur adipiscing elit, sed do eiusmod tempor incididunt ut labore et dolore magna aliqua. Ut enim ad minim veniam, quis nostrud exercitation ullamco laboris nisi ut aliquip ex ea commodo consequat.
  </div>
  <div class="btn-outline" style="left:779px;top:1114px;width:101px;height:34px">Read More</div>
  <div class="abs dots" style="left:804px;top:1203px"><span></span><span></span><span></span><span></span></div>
</section>

<!-- Biography -->
<section>
  <h2 class="abs bio-title display">My Biography</h2>
  <p class="abs bio-text" style="top:1460px">Duis aute irure dolor in reprehenderit in voluptate velit esse cillum dolore eu fugiat nulla pariatur. Excepteur sint occaecat cupidatat non proident, sunt in culpa qui officia deserunt mollit anim id est laborum.</p>
  <p class="abs bio-text" style="top:1589px">Sed ut perspiciatis unde omnis iste natus error sit voluptatem accusantium doloremque laudantium, totam rem aperiam, eaque ipsa quae ab illo inventore veritatis et quasi architecto beatae vitae dicta sunt explicabo.</p>
  <div class="btn-outline" style="left:112px;top:1757px;width:101px;height:35px">Read More</div>
  <div class="abs frame" style="left:656px;top:1310px;width:385px;height:200px;border-bottom:none;border-radius:10px 10px 0 0"></div>
  <div class="photo" style="left:678px;top:1331px;width:410px;height:514px;background:linear-gradient(180deg,#cfe0ea 0%,#b9cfdc 45%,#e8c9cd 70%,#a8b88a 100%)" role="img" aria-label="Bride and groom kissing by a lake"></div>
  <div class="photo" style="left:622px;top:1561px;width:191px;height:245px;border-radius:4px;background:linear-gradient(180deg,#c7c3bd 0%,#9aa5ad 50%,#2f5a6e 100%)" role="img" aria-label="Portrait of the photographer holding a camera"></div>
</section>

<!-- Gallery -->
<section>
  <h2 class="section-title display" style="top:1927px">Gallery</h2>
  <p class="abs gallery-intro">Lorem ipsum dolor sit amet, consectetur adipiscing elit, sed do eiusmod tempor incididunt ut labore et dolore magna aliqua. Ut enim ad minim veniam, quis nostrud exercitation ullamco laboris nisi ut aliquip ex ea commodo consequat.</p>
  <div class="photo" style="left:110px;top:2125px;width:477px;height:252px;background:linear-gradient(180deg,#1c2b4f 0%,#2f4470 45%,#c4753e 60%,#3b4030 100%)" role="img" aria-label="Couple dancing on a hill under a dramatic evening sky"></div>
  <div class="photo" style="left:609px;top:2125px;width:477px;height:252px;background:linear-gradient(180deg,#6e7c97 0%,#b9c0cb 45%,#e9e2cf 60%,#5b6a3c 100%)" role="img" aria-label="Couple walking across a field toward the sun"></div>
  <div class="photo" style="left:110px;top:2402px;width:253px;height:228px;background:linear-gradient(180deg,#cfd8de 0%,#b9c3b4 50%,#6d7a48 100%)" role="img" aria-label="Bride and groom standing in a meadow"></div>
  <div class="photo" style="left:383px;top:2402px;width:424px;height:476px;background:linear-gradient(180deg,#454b5d 0%,#6b6d7d 40%,#c9957b 62%,#3c3a3c 100%)" role="img" aria-label="Couple holding hands on a cliff at dusk"></div>
  <div class="photo" style="left:834px;top:2402px;width:252px;height:228px;background:linear-gradient(135deg,#7d6a3a 0%,#c8a45a 40%,#2c3036 75%,#e8e6e2 100%)" role="img" aria-label="Smiling bride and groom close together"></div>
  <div class="photo" style="left:110px;top:2652px;width:253px;height:226px;background:linear-gradient(135deg,#e8e2dc 0%,#f4f2ee 45%,#2a2a2a 70%,#6f8a4a 100%)" role="img" aria-label="Bride holding a white orchid bouquet"></div>
  <div class="photo" style="left:834px;top:2652px;width:252px;height:226px;background:linear-gradient(135deg,#7a2e2e 0%,#b7a38a 45%,#eee9e1 100%)" role="img" aria-label="Photographer shooting a seated bride indoors"></div>
  <div class="photo" style="left:110px;top:2901px;width:477px;height:254px;background:linear-gradient(180deg,#2e2a33 0%,#b76a3a 50%,#f3b25a 62%,#1e1a18 100%)" role="img" aria-label="Couple silhouetted at sunrise with hot air balloons"></div>
  <div class="photo" style="left:609px;top:2901px;width:477px;height:254px;background:linear-gradient(135deg,#6b4a33 0%,#8b6647 40%,#eeeae4 60%,#d9d6d0 100%)" role="img" aria-label="Bride lying on a wooden floor photographed from above"></div>
</section>

<!-- Price -->
<section>
  <h2 class="section-title display" style="top:3241px">Our Price</h2>
  <div class="abs price-band" role="img" aria-label="Dark background photo of a couple"></div>
  <div class="tab display" style="left:204px;width:383px;background:var(--accent);color:var(--white)">Landscape
    <svg style="position:absolute;right:36px;top:24px" width="30" height="30" viewBox="0 0 30 30"><g stroke="#fff" stroke-width="2"><path d="M6 3v5M0 9h5M2 3l3 3M10 3 8 6"/></g><path d="M10 10 L26 16 L19 18 L24 25 L21 27 L16 20 L12 25 Z" fill="#fff"/></svg>
  </div>
  <div class="tab display" style="left:617px;width:381px;background:var(--white);color:var(--accent);box-shadow:0 2px 8px rgba(0,0,0,.1)">Portrait</div>
  <div class="price-card" style="left:114px"><h3 class="display">1 Package</h3><p>Lorem ipsum dolor sit amet consectetur. Ac lobortis risus ultrices massa commodo ut. Orci</p><strong>$ 150</strong></div>
  <div class="price-card" style="left:458px"><h3 class="display">2 Package</h3><p>Lorem ipsum dolor sit amet consectetur. Ac lobortis risus ultrices massa commodo ut. Orci</p><strong>$ 200</strong></div>
  <div class="price-card" style="left:800px"><h3 class="display">3 Package</h3><p>Lorem ipsum dolor sit amet consectetur. Ac lobortis risus ultrices massa commodo ut. Orci</p><strong>$ 250</strong></div>
</section>

<!-- Testimonials -->
<section>
  <div class="photo" style="left:112px;top:3861px;width:445px;height:522px;background:linear-gradient(180deg,#c9a7a4 0%,#a8a3ae 45%,#d9cfc8 75%,#e9e3dc 100%)" role="img" aria-label="Couple kissing by the sea, bride wearing a flower crown"></div>
  <h2 class="abs display" style="left:649px;top:3922px;width:400px;text-align:center;color:var(--accent);font-size:42px;line-height:1">Testimonials</h2>
  <div class="abs quote-mark display" style="left:628px;top:4005px">“</div>
  <p class="abs quote-text">Duis aute irure dolor in reprehenderit in voluptate velit esse cillum dolore eu fugiat nulla pariatur. Excepteur sint occaecat cupidatat non proident, sunt in culpa qui officia deserunt mollit anim id est laborum.”</p>
  <div class="abs quote-mark display" style="left:946px;top:4097px">”</div>
  <div class="avatar" style="left:725px;top:4196px;width:56px;height:56px;background:#d8c8c0" role="img" aria-label="Client photo"></div>
  <div class="avatar" style="left:770px;top:4196px;width:56px;height:56px;background:#cdb9ad" role="img" aria-label="Client photo"></div>
  <div class="avatar" style="left:912px;top:4196px;width:56px;height:56px;background:#e2d3c9" role="img" aria-label="Client photo"></div>
  <div class="avatar" style="left:868px;top:4192px;width:62px;height:62px;background:#c8b2a6" role="img" aria-label="Client photo"></div>
  <div class="avatar" style="left:811px;top:4182px;width:82px;height:82px;background:#6a5548" role="img" aria-label="Featured client photo"></div>
  <div class="abs dots" style="left:813px;top:4313px"><span style="border-radius:0;width:7px;height:7px"></span><span style="border-radius:0;width:7px;height:7px"></span><span style="border-radius:0;width:7px;height:7px"></span><span style="border-radius:0;width:7px;height:7px"></span><span style="border-radius:0;width:7px;height:7px"></span></div>
</section>

<!-- Footer -->
<footer>
  <div class="abs footer"></div>
  <div class="abs footer-brand">LUMERA</div>
  <nav class="footer-nav">
    <a style="left:340px">Home</a>
    <a style="left:434px">Blog</a>
    <a style="left:516px">Testimonials</a>
    <a style="left:658px">Portfolio</a>
    <a style="left:768px">Get In Touch</a>
  </nav>
  <span class="social" style="left:521px"></span>
  <span class="social" style="left:555px"></span>
  <span class="social" style="left:589px"></span>
  <span class="social" style="left:623px"></span>
  <span class="social" style="left:656px"></span>
  <div class="abs footer-rule"></div>
  <p class="abs copyright">Copyright © 2023 Lumera.All rights reserved.</p>
</footer>

</body>
</html>
```